Tovel & Associates - London New Letting and Property Management Company *

Tovel & Associates LTD is a new company based in London, and works with brand new residential property in the city centre.

We are aiming to have 1000 new properties a year.

We are looking for something modern and minimalistic :
Logo ,Monogram, Paper Head and Business Card.

Target Market(s)

Internation landlords

Industry/Entity Type

Real Estate

Logo Text

Tovel & Associates

Colors

Designer to choose colors to be used in the design.

Requirements
Nice to have
• A particular monogram with "TA"
Should not have
• Little House over the logo

```html
<!DOCTYPE html>
<html lang="en">
<head>
<meta charset="utf-8">
<title>Tovel &amp; Associates – Stationery</title>
<link href="https://fonts.googleapis.com/css2?family=Work+Sans:wght@400;500;600&display=swap" rel="stylesheet">
<style>
  :root{
    --backdrop:#dcdcdc;
    --paper:#f3f3f3;
    --navy:#1c4e72;
    --sky:#29a9e1;
    --ink:#6a6a6a;
    --ink-dark:#4a4a4a;
    --white:#ffffff;
  }
  *{margin:0;padding:0;box-sizing:border-box}
  html,body{width:1200px;height:1062px;overflow:hidden;background:var(--backdrop)}
  body{position:relative;font-family:'Work Sans',sans-serif;color:var(--ink)}
  .sheet,.card{position:absolute;background:var(--paper);box-shadow:0 2px 8px rgba(0,0,0,.18)}
  .band{position:absolute;top:0;background:var(--sky)}
  .wordmark{position:absolute;font-family:'Work Sans',sans-serif;font-weight:600;color:var(--navy);letter-spacing:.04em;text-transform:uppercase;white-space:nowrap}

  /* letterhead */
  .letterhead{left:115px;top:94px;width:620px;height:876px}
  .letterhead .band{left:83px;width:85px;height:34px}
  .letterhead .wordmark{left:40px;top:134px;font-size:15px}
  .salutation{position:absolute;left:42px;top:188px;font-size:17px;color:var(--ink-dark)}
  .body-copy{position:absolute;left:42px;top:242px;width:540px}
  .body-copy p{font-size:11.8px;line-height:16.3px;margin-bottom:20px;color:var(--ink)}
  .closing{position:absolute;left:42px;top:628px}
  .closing .regards{font-size:14px;color:var(--ink-dark)}
  .signature{display:block;width:112px;height:18px;margin:11px 0 12px;background:linear-gradient(90deg,rgba(80,80,80,.25),rgba(80,80,80,.1))}
  .closing .name{font-size:13.5px;color:var(--ink-dark)}
  .closing .role{font-size:11px;color:var(--ink-dark);margin-top:1px}
  .closing .company{font-size:8px;font-weight:600;color:var(--ink-dark);text-transform:uppercase;margin-top:4px}
  .rule{position:absolute;height:2px;background:var(--navy)}
  .letterhead .rule{left:40px;top:764px;width:541px}
  .contacts{position:absolute;list-style:none}
  .contacts li{display:flex;align-items:center;gap:6px;color:var(--ink)}
  .contacts svg{flex:none}
  .contacts b{color:var(--navy);font-weight:500}
  .letterhead .contacts{left:40px;top:788px;font-size:12px;line-height:15.6px}
  .address{position:absolute;text-align:right;color:var(--ink)}
  .letterhead .address{right:39px;top:810px;font-size:12px;line-height:15.6px}

  /* standalone logo */
  .logo-lockup{position:absolute;left:800px;top:134px;width:290px;height:190px}
  .logo-lockup .mark{position:absolute;left:97px;top:0;width:96px;height:96px;background:var(--navy)}
  .logo-lockup .wordmark{left:0;top:150px;width:290px;text-align:center;font-size:25px}

  /* business card front */
  .card-front{left:716px;top:475px;width:374px;height:213px}
  .card-front .band{left:42px;width:50px;height:23px}
  .card-front .wordmark{left:17px;top:80px;font-size:9.5px}
  .holder{position:absolute;right:18px;top:112px;text-align:right}
  .holder .name{font-size:14.5px;color:var(--navy);text-transform:uppercase;letter-spacing:.02em}
  .holder .role{font-size:9px;color:var(--ink);margin-top:2px}
  .card-front .rule{left:17px;top:149px;width:339px;height:1.5px}
  .card-front .contacts{left:17px;top:162px;font-size:9px;line-height:13px}
  .card-front .contacts li{gap:4px}
  .card-front .address{right:18px;top:175px;font-size:9px;line-height:13px}

  /* business card back */
  .card-back{left:716px;top:726px;width:374px;height:213px;background:var(--navy)}
  .card-back .mark{position:absolute;left:164px;top:58px;width:46px;height:46px;border:3px solid var(--white)}
  .card-back .wordmark{left:0;top:150px;width:374px;text-align:center;font-size:14.5px;color:var(--white)}
</style>
</head>
<body>

<section class="sheet letterhead">
  <div class="band"></div>
  <div class="wordmark">Tovel &amp; Associates</div>
  <h1 class="salutation" style="font-weight:400">Dear Sir</h1>
  <div class="body-copy">
    <p>Lorem ipsum dolor sit amet, an vel recteque dissentiet, detracto albucius platonem ex vel, eros repudiandae cu. Atqui aliquando nec an, unum graece adolescens vel ad. Id odio scae has, iudico euismod atomorum ius ea, cum ea honestatis quaerendum theophrastus. Mea honestatis quaerendum theophrastus. Mea</p>
    <p>Lorem ipsum dolor sit amet, an vel recteque dissentiet, detracto albucius platonem ex vel, eros repudiandae cu. Atqui aliquando nec an, unum graece adolescens vel ad. Id odio scae has, iudico euismod atomorum ius ea, cum ea honestatis quaerendum theophrastus. Mea doming repudiandae ex, cu cum civibus assentior posidonium. Quo etiam pertinax ex, te eros repudiandae cu. Atqui aliquando nec an, unum graece adolescens vel ad. Id odio scae honestatis quaerendum theophrastus. Mea</p>
    <p>Lorem ipsum dolor sit amet, an vel recteque dissentiet, detracto albucius platonem ex vel, eros repudiandae cu. Atqui aliquando nec an, unum graece adolescens vel ad. Id odio scae has, iudico euismod atomorum ius ea, cum ea honestatis quaerendum theophrastus. Mea honestatis quaerendum theophrastus. Mea</p>
    <p>Lorem ipsum dolor sit amet, an vel recteque dissentiet, detracto albucius platonem ex vel, eros repudiandae cu. Atqui aliquando nec an, unum graece adolescens vel ad. Id odio scae has, iudico euismod atomorum ius ea, cum ea honestatis quaerendum theophrastus. Mea honestatis quaerendum theophrastus. Mea</p>
  </div>
  <div class="closing">
    <div class="regards">Kind Regards</div>
    <span class="signature" role="img" aria-label="Handwritten signature of Oliver Whitcombe"></span>
    <div class="name">Oliver Whitcombe</div>
    <div class="role">Chief Alchemist</div>
    <div class="company">Harrowgate Estate Holdings Ltd</div>
  </div>
  <div class="rule"></div>
  <ul class="contacts">
    <li><svg width="8" height="8" viewBox="0 0 10 10"><path d="M2 0h2l1 3-1.5 1a6 6 0 0 0 2.5 2.5L7 5l3 1v2a2 2 0 0 1-2 2A8 8 0 0 1 0 2a2 2 0 0 1 2-2z" fill="#1c4e72"/></svg>+44 20 7946 0321</li>
    <li><svg width="8" height="8" viewBox="0 0 10 10"><rect x="0.5" y="2" width="9" height="6" fill="none" stroke="#1c4e72"/><path d="M0.5 2l4.5 3.5L9.5 2" fill="none" stroke="#1c4e72"/></svg>info@tovelassociates.com</li>
    <li><svg width="8" height="8" viewBox="0 0 10 10"><circle cx="5" cy="5" r="4.3" fill="none" stroke="#1c4e72"/><path d="M1 5h8M5 1v8" stroke="#1c4e72"/></svg>www.<b>tovelassociates</b>.com</li>
  </ul>
  <div class="address">14 Crane Court<br>London EC4A 2EJ</div>
</section>

<section class="logo-lockup">
  <div class="mark"></div>
  <div class="wordmark">Tovel &amp; Associates</div>
</section>

<section class="card card-front">
  <div class="band"></div>
  <div class="wordmark">Tovel &amp; Associates</div>
  <div class="holder">
    <div class="name">Daniel Hartley</div>
    <div class="role">Director</div>
  </div>
  <div class="rule"></div>
  <ul class="contacts">
    <li><svg width="6" height="6" viewBox="0 0 10 10"><path d="M2 0h2l1 3-1.5 1a6 6 0 0 0 2.5 2.5L7 5l3 1v2a2 2 0 0 1-2 2A8 8 0 0 1 0 2a2 2 0 0 1 2-2z" fill="#1c4e72"/></svg>+44 20 7946 0321</li>
    <li><svg width="6" height="6" viewBox="0 0 10 10"><rect x="0.5" y="2" width="9" height="6" fill="none" stroke="#1c4e72"/><path d="M0.5 2l4.5 3.5L9.5 2" fill="none" stroke="#1c4e72"/></svg>info@tovelassociates.com</li>
    <li><svg width="6" height="6" viewBox="0 0 10 10"><circle cx="5" cy="5" r="4.3" fill="none" stroke="#1c4e72"/><path d="M1 5h8M5 1v8" stroke="#1c4e72"/></svg>www.<b>tovelassociates</b>.com</li>
  </ul>
  <div class="address">14 Crane Court<br>London EC4A 2EJ</div>
</section>

<section class="card card-back">
  <div class="mark"></div>
  <div class="wordmark">Tovel &amp; Associates</div>
</section>

</body>
</html>
```